New Business Card Design Project LORVANTI-Italy

we are LORVANTI-Italy
our company in the market for 3 years we are luxury cosmetic company and its about time for a facelift :)
i will like to have elegant luxurious and unique business card
that will give the person that get it a unique, luxurious and elegant impression
I'm VERY OPEN FOR NEW IDEAS , even duo i add a few files of things that i see on line and i like them

i add my logo as well
my website is LORVANTI.COM
(if you would like to see the main style that we have)

Target Market(s)

adult that have money :)

Industry/Entity Type

Business

Contact Information for Business Card

Name - Dario Lorvanti
Position - CEO and CO Founder
address - 4817 E Halvern
telephone - 555-384-1926
email - dario@lorvanti.com
fax - 555-384-1926
website - LORVANTI.COM

Colors
000000
959595
fbee3e
ffffff

Requirements
Must have
• big logo in GOLD color
• elegant look
• impressive
Nice to have
• not must but maybe classy pattern background
• not must but maybe emblem
• maybe clear plastic business card
Should not have
• colors
• images

```html
<!DOCTYPE html>
<html lang="en">
<head>
<meta charset="UTF-8">
<title>Dario Lorvanti – Business Card</title>
<link rel="stylesheet" href="https://fonts.googleapis.com/css2?family=Share+Tech+Mono&display=swap">
<style>
  :root {
    --card-black: #0b0b0b;
    --card-charcoal: #2a2a2a;
    --gold: #d9b54a;
    --gold-soft: #e0b64c;
    --white: #ffffff;
  }
  * { margin: 0; padding: 0; box-sizing: border-box; }
  html, body {
    width: 1200px;
    height: 760px;
    overflow: hidden;
    background: var(--card-black);
  }
  .card {
    position: relative;
    width: 1200px;
    height: 760px;
    overflow: hidden;
    font-family: "Share Tech Mono", monospace;
  }
  .card-texture {
    position: absolute;
    inset: 0;
    background: radial-gradient(ellipse at 45% 30%, var(--card-charcoal) 0%, #1a1a1a 45%, var(--card-black) 100%);
  }
  .holder-name {
    position: absolute;
    left: 113px;
    top: 62px;
    font-size: 84px;
    line-height: 1;
    color: var(--white);
    font-weight: 400;
    letter-spacing: 1px;
  }
  .holder-title {
    position: absolute;
    left: 115px;
    top: 170px;
    font-size: 40px;
    line-height: 1;
    font-style: italic;
    color: var(--gold-soft);
  }
  .brand {
    position: absolute;
    left: 146px;
    top: 474px;
    width: 260px;
    display: flex;
    flex-direction: column;
    align-items: center;
    gap: 28px;
  }
  .brand-circle {
    display: block;
  }
  .brand-name {
    font-size: 44px;
    line-height: 1;
    color: var(--gold);
    letter-spacing: 2px;
  }
  .divider {
    position: absolute;
    left: 618px;
    top: 508px;
    width: 3px;
    height: 162px;
    background: var(--white);
  }
  .contact {
    position: absolute;
    left: 674px;
    top: 514px;
    list-style: none;
    color: var(--white);
    font-size: 42px;
    font-style: italic;
    line-height: 52px;
    letter-spacing: 2px;
  }
</style>
</head>
<body>
  <main class="card">
    <div class="card-texture" role="img" aria-label="Dark diagonal pinstripe background texture"></div>

    <h1 class="holder-name">Dario Lorvanti</h1>
    <p class="holder-title">CEO and CO Founder</p>

    <div class="brand">
      <svg class="brand-circle" width="118" height="118" viewBox="0 0 118 118" aria-hidden="true">
        <circle cx="59" cy="59" r="57" fill="var(--gold)"/>
      </svg>
      <span class="brand-name">LORVANTI</span>
    </div>

    <div class="divider"></div>

    <ul class="contact">
      <li class="contact-address">4817 E Halvern</li>
      <li class="contact-phone">555-384-1926</li>
      <li class="contact-email">dario@lorvanti.com</li>
    </ul>
  </main>
</body>
</html>
```